Fun Employee News and Engagement Portal - Tidy Hearth Company

We are looking for a clean, but fun WordPress template for an internal employee engagement website. The site will be a place we share news, fun stories and pictures. We'll provide space for our employees to post comments, etc.
We are a deep dish pizza restaurant with a rich history. I'd love to see your take on a look and feel for us! The site will be called Bim-Zee. I've posted some images and colors along with this brief description.
Focus on making the template whimsical and fun! (Extra point for focusing on the "Lettering in lights" ).
I will continue to post additional pieces of art and content examples.
Reason: Our team is continuing to review designs. We've decided to extend the timing a few more days. Good luck! Make it playful!
Reason: We need more time with our team to review these designs. We are going to extend one more time!
Reason: Still trying to get enough time to review with the Bim-Zee team!
Reason: We are continuing to evaluate designs. Thank you!
Industry/Entity Type
American Restaurant
Number of Pages Required
1 page
Look and feel
Each slider illustrates characteristics of the customer's brand and the style your logo design should communicate.

```html
<!DOCTYPE html>
<html lang="en">
<head>
<meta charset="utf-8">
<title>Bim-Zee</title>
<link href="https://fonts.googleapis.com/css2?family=Bree+Serif&family=Open+Sans:wght@400;600;700&display=swap" rel="stylesheet">
<style>
:root{
  --red:#e3202f;
  --ink:#333333;
  --muted:#666666;
  --light:#f5f5f5;
  --lighter:#f8f8f8;
  --badge:#dcdcdc;
  --footer:#4a4a4a;
  --white:#ffffff;
}
*{margin:0;padding:0;box-sizing:border-box}
html,body{width:1200px;height:2267px;overflow:hidden}
body{position:relative;background:var(--white);font-family:"Open Sans",sans-serif;color:var(--ink)}
.abs{position:absolute}
.slab{font-family:"Bree Serif",serif;font-weight:400}

/* hero */
.hero{left:0;top:0;width:1200px;height:590px;
  background:radial-gradient(ellipse 560px 300px at 600px 360px,#c9803f 0%,#b3552e 35%,#6f4a3a 62%,#4a4644 85%,#3b3b3b 100%)}
.brand{left:133px;top:44px;font-size:34px;line-height:40px;color:var(--white);z-index:2}
.social{right:133px;top:22px;display:flex;gap:20px;z-index:2}
.social span{width:15px;height:15px;border-radius:50%;background:var(--white);display:block}
.nav{right:133px;top:68px;display:flex;gap:44px;font-size:11px;line-height:14px;color:var(--white);text-transform:uppercase;z-index:2}
.hero-title{left:0;width:1200px;top:212px;text-align:center;font-size:56px;line-height:66px;color:var(--white);text-shadow:0 2px 6px rgba(0,0,0,.35)}
.hero-sub{left:0;width:1200px;top:299px;text-align:center;font-size:14px;line-height:18px;color:var(--white);text-transform:uppercase;text-shadow:0 1px 3px rgba(0,0,0,.5)}
.btn{background:var(--red);color:var(--white);font-size:11px;text-transform:uppercase;display:flex;align-items:center;justify-content:center;border-radius:3px}
.hero-btn{left:536px;top:349px;width:129px;height:42px}
.dots{left:580px;top:532px;display:flex;gap:6px}
.dots span{width:8px;height:8px;border-radius:50%;background:rgba(255,255,255,.5)}
.dots span:first-child{background:var(--white)}

/* partner band */
.partners{left:0;top:590px;width:1200px;height:122px;background:var(--light);border-bottom:1px solid #e2e2e2}
.badge{position:absolute;top:30px;height:62px;background:var(--badge);border-radius:8px}

/* welcome */
.section-title{font-size:34px;line-height:40px;color:var(--red);text-transform:uppercase}
.welcome-title{left:133px;top:790px}
.copy{font-size:11px;line-height:24px;color:var(--muted);text-align:justify}
.welcome-copy{left:133px;top:862px;width:505px}
.read-btn{left:133px;top:991px;width:103px;height:41px}
.welcome-photo{left:700px;top:768px;width:426px;height:312px;border-radius:20px;
  background:radial-gradient(ellipse at center,#e6a04a 0%,#d98a3a 45%,#f2d2a0 75%,#ffffff 100%)}

/* stories */
.stories{left:0;top:1124px;width:1200px;height:345px;background:var(--lighter)}
.centered{left:0;width:1200px;text-align:center}
.stories-title{top:1172px}
.avatar{width:133px;height:133px;border-radius:50%;top:1262px}
.av-1{left:133px;background:linear-gradient(135deg,#3d5a7a,#c08a64)}
.av-2{left:620px;background:linear-gradient(135deg,#6f8a4a,#d7b89a)}
.story-copy{top:1268px;width:284px}

/* news */
.news-title{top:1544px}
.card-img{top:1624px;width:296px;height:161px}
.img-1{background:linear-gradient(135deg,#a9c6cf,#e5b78a)}
.img-2{background:linear-gradient(135deg,#5a3a24,#c6703c)}
.img-3{background:linear-gradient(135deg,#8a5a34,#d8603a)}
.card-title{top:1802px;font-size:15px;line-height:20px;letter-spacing:3px;color:var(--red);text-transform:uppercase}
.card-date{top:1829px;font-size:10px;color:var(--muted)}
.card-copy{top:1852px;width:296px}
.card-more{top:1935px;font-size:10px;color:var(--red);text-transform:uppercase}

/* footer */
.footer{left:0;top:2020px;width:1200px;height:247px;background:var(--footer)}
.foot-head{top:2060px;font-size:14px;line-height:18px;color:var(--white);text-transform:uppercase}
.quick{left:135px;top:2094px;font-size:11px;line-height:19px;color:var(--white);list-style:none}
.foot-social{left:304px;top:2098px;display:flex;gap:18px}
.foot-social span{width:16px;height:16px;border-radius:50%;background:var(--white);display:block}
.field{background:var(--white);font-size:9px;letter-spacing:1px;color:#999;padding:7px 10px;text-transform:uppercase}
.submit{left:979px;top:2185px;width:88px;height:29px;font-size:11px;border-radius:0}
.copyright{left:133px;top:2220px;font-size:11px;font-weight:700;color:var(--white)}
</style>
</head>
<body>

<div class="abs hero" role="img" aria-label="Close-up photo of a fresh pizza topped with tomato, mozzarella and greens"></div>
<div class="abs brand slab">Bim-Zee</div>
<div class="abs social" aria-label="Social links"><span></span><span></span><span></span><span></span></div>
<nav class="abs nav slab"><span>Home</span><span>About us</span><span>Menu</span><span>News</span><span>Contact</span></nav>
<h1 class="abs hero-title slab">TIDY HEARTH</h1>
<p class="abs hero-sub slab">Nemo enim ipsam voluptatem quia voluptas sit aspernatur aut odit aut fugit</p>
<div class="abs btn hero-btn slab">View details</div>
<div class="abs dots"><span></span><span></span><span></span></div>

<div class="abs partners" aria-label="Partner badges">
  <div class="badge" style="left:177px;width:180px"></div>
  <div class="badge" style="left:408px;width:212px"></div>
  <div class="badge" style="left:668px;width:190px"></div>
  <div class="badge" style="left:905px;width:112px;border-radius:50%"></div>
</div>

<h2 class="abs section-title slab welcome-title">Welcome to Bim-Zee</h2>
<p class="abs copy welcome-copy">Nemo enim ipsam voluptatem quia voluptas sit aspernatur aut odit aut fugit, sed quia consequuntur magni dolores eos qui ratione voluptatem sequi nesciunt. Neque porro quisquam est, qui dolorem ipsum quia dolor sit amet, consectetur, adipisci velit, sed quia non numquam eius modi tempora incidunt ut labore et dolore magnam aliquam quaerat voluptatem.</p>
<div class="abs btn read-btn slab">Read more</div>
<div class="abs welcome-photo" role="img" aria-label="Stack of cheese pizza slices"></div>

<div class="abs stories"></div>
<h2 class="abs section-title slab centered stories-title">Fun Stories</h2>
<div class="abs avatar av-1" role="img" aria-label="Group of friends sharing pizza"></div>
<p class="abs copy story-copy" style="left:295px">Nemo enim ipsam voluptatem quia voluptas sit aspernatur aut odit aut fugit, sed quia consequuntur magni dolores eos qui ratione voluptatem sequi nesciunt. Neque porro quisquam est, qui dolorem ipsum quia dolor sit amet, consectetur</p>
<div class="abs avatar av-2" role="img" aria-label="Couple eating pizza outdoors"></div>
<p class="abs copy story-copy" style="left:783px">Nemo enim ipsam voluptatem quia voluptas sit aspernatur aut odit aut fugit, sed quia consequuntur magni dolores eos qui ratione voluptatem sequi nesciunt. Neque porro quisquam est, qui dolorem ipsum quia dolor sit amet, consectetur</p>

<h2 class="abs section-title slab centered news-title">Employee News</h2>

<div class="abs card-img img-1" style="left:133px" role="img" aria-label="Pizza slice close-up"></div>
<h3 class="abs card-title slab" style="left:133px">Tidy Hearth</h3>
<div class="abs card-date" style="left:133px">JAN 06,2015</div>
<p class="abs copy card-copy" style="left:133px">Nemo enim ipsam voluptatem quia voluptas sit aspernatur aut odit aut fugit, sed quia consequuntur magni dolores eos qui ratione</p>
<div class="abs card-more" style="left:133px">Read more &rsaquo;</div>

<div class="abs card-img img-2" style="left:452px" role="img" aria-label="Sliced pizza on a wooden board"></div>
<h3 class="abs card-title slab" style="left:452px">Tidy Hearth</h3>
<div class="abs card-date" style="left:452px">JAN 06,2015</div>
<p class="abs copy card-copy" style="left:452px">Nemo enim ipsam voluptatem quia voluptas sit aspernatur aut odit aut fugit, sed quia consequuntur magni dolores eos qui ratione</p>
<div class="abs card-more" style="left:452px">Read more &rsaquo;</div>

<div class="abs card-img img-3" style="left:772px" role="img" aria-label="Pizza with fresh tomatoes and vegetables"></div>
<h3 class="abs card-title slab" style="left:772px">Tidy Hearth</h3>
<div class="abs card-date" style="left:772px">JAN 06,2015</div>
<p class="abs copy card-copy" style="left:772px">Nemo enim ipsam voluptatem quia voluptas sit aspernatur aut odit aut fugit, sed quia consequuntur magni dolores eos qui ratione</p>
<div class="abs card-more" style="left:772px">Read more &rsaquo;</div>

<footer class="abs footer"></footer>
<h4 class="abs foot-head slab" style="left:133px">Quick links</h4>
<ul class="abs quick"><li>Home</li><li>About us</li><li>Menu</li><li>News</li><li>Contact</li></ul>
<h4 class="abs foot-head slab" style="left:304px;top:2056px">Follow us</h4>
<div class="abs foot-social"><span></span><span></span><span></span><span></span></div>
<h4 class="abs foot-head slab" style="left:535px">Post comments</h4>
<div class="abs field" style="left:536px;top:2105px;width:262px;height:27px">First name</div>
<div class="abs field" style="left:536px;top:2141px;width:262px;height:27px">Email</div>
<div class="abs field" style="left:805px;top:2105px;width:262px;height:63px">Message</div>
<div class="abs btn submit slab">Submit</div>
<div class="abs copyright">&copy; 2017 BIM-ZEE.</div>

</body>
</html>
```